Business Card Design

We like to use greens as you will see in our logo (but not TOO much green). We are a Dental Clinic in a somewhat eccentric community. We do not like the dated sharp designs which we see many dentists use. We're looking for something bright and fresh while still maintaining the integrity of the profession. Elegance is not necessarily what we are going for... we need for the design to be "mature" but also up-lifting.

See our logo.
Updates

Project Deadline Extended
Reason: We have 5 designs which we like. But we'd like to see a few more before committing to a design.

Project Deadline Extended
Reason: We are awaiting revisions to this project. We are still welcoming designs while we wait to see if designers are able to provide to us the revisions we require in order to proceed with a selection.

Target Market(s)

Younger families - ages late 20's to early 40's

Industry/Entity Type

Business

Contact Information for Business Card

Corwel T. Banfry DDS 2730 W. Halvert Rd. Ste. 7 Alderbrook, WA 48391 (248)555-0174 FX (248)555-0189 info@BrightwellDentalCareMi.com BrigthwellDentalCareMi.com on the back of the card we need an appointment reminder (For____ Date___ Time____) with "If you are unable to keep your appointment, kindly give 48 hours notice" at the bottom. No use of teeth in the design. DOUBLE SIDED DESIGN

Requirements
Should not have
• The use of pictures of teeth

```html
<!DOCTYPE html>
<html lang="en">
<head>
<meta charset="utf-8">
<title>Brightwell Dental Care – Business Card</title>
<link href="https://fonts.googleapis.com/css2?family=Arimo:wght@400;700&family=Tinos:ital,wght@0,400;0,700;1,400&display=swap" rel="stylesheet">
<style>
  :root {
    --bg: #ebe7e2;
    --card: #ffffff;
    --green-deep: #2f7a1c;
    --green-band: #2e7d1e;
    --green-lime: #8ed630;
    --ink: #333333;
    --ink-soft: #666666;
    --rule: #9a9a9a;
  }
  * { box-sizing: border-box; margin: 0; padding: 0; }
  html, body { width: 1200px; height: 492px; overflow: hidden; }
  body {
    background: var(--bg);
    font-family: "Arimo", Arial, sans-serif;
    color: var(--ink);
    position: relative;
  }
  .card {
    position: absolute;
    top: 103px;
    width: 500px;
    height: 286px;
    background: var(--card);
    box-shadow: 0 6px 18px rgba(0,0,0,0.25);
    overflow: hidden;
  }
  .card--front { left: 70px; }
  .card--back { left: 630px; }

  .front-swoosh { position: absolute; inset: 0; }

  .doctor {
    position: absolute;
    top: 24px;
    right: 26px;
    text-align: right;
    color: #fff;
  }
  .doctor__name { font-weight: 700; font-size: 20px; letter-spacing: 0.2px; }
  .doctor__title { font-size: 12px; margin-top: 4px; }

  .brand {
    position: absolute;
    display: flex;
    align-items: center;
    gap: 8px;
  }
  .brand__dot {
    width: 14px; height: 14px; border-radius: 50%;
    background: var(--green-deep);
    flex: none;
  }
  .brand__name {
    font-weight: 700;
    color: var(--green-deep);
    line-height: 1.05;
  }
  .brand__sub { display: block; font-size: 0.55em; letter-spacing: 1px; }
  .card--front .brand { left: 34px; top: 114px; }
  .card--front .brand__name { font-size: 34px; }
  .card--back .brand { left: 34px; top: 40px; }
  .card--back .brand__name { font-size: 30px; }

  .contact {
    position: absolute;
    left: 30px;
    bottom: 20px;
    list-style: none;
    font-size: 13.5px;
    line-height: 20px;
  }
  .contact li { display: flex; align-items: center; gap: 6px; }
  .contact svg { width: 11px; height: 11px; flex: none; }

  .address {
    position: absolute;
    left: 264px;
    top: 196px;
    padding-left: 14px;
    border-left: 1px solid var(--rule);
    font-size: 13.5px;
    line-height: 20px;
    font-style: normal;
  }

  .appointment { position: absolute; left: 34px; right: 26px; top: 146px; }
  .appointment__title {
    font-family: "Tinos", "Times New Roman", serif;
    font-weight: 700;
    color: var(--green-deep);
    font-size: 16px;
    display: flex;
    align-items: flex-end;
    gap: 6px;
  }
  .appointment__title::after {
    content: "";
    width: 170px;
    border-bottom: 1px dotted var(--rule);
    margin-bottom: 4px;
  }
  .field-row {
    display: flex;
    align-items: flex-end;
    gap: 6px;
    font-size: 15px;
    color: var(--ink-soft);
    margin-top: 18px;
  }
  .field-line { border-bottom: 1px solid var(--rule); height: 1px; margin-bottom: 3px; }
  .field-line--dotted { border-bottom-style: dotted; }
  .notice {
    position: absolute;
    left: 28px;
    right: 14px;
    bottom: 16px;
    font-family: "Tinos", "Times New Roman", serif;
    font-style: italic;
    font-size: 16px;
    color: var(--ink-soft);
    white-space: nowrap;
  }
</style>
</head>
<body>

  <section class="card card--front" aria-label="Business card front">
    <svg class="front-swoosh" viewBox="0 0 500 286" preserveAspectRatio="none" aria-hidden="true">
      <path d="M0,0 H500 V190 C430,70 230,18 0,22 Z" fill="var(--green-band)"/>
      <path d="M0,33 C230,30 430,85 500,205" fill="none" stroke="var(--green-lime)" stroke-width="6"/>
    </svg>

    <div class="doctor">
      <div class="doctor__name">Corwel T. Banfry</div>
      <div class="doctor__title">DDS</div>
    </div>

    <div class="brand">
      <span class="brand__dot"></span>
      <span class="brand__name">Brightwell<span class="brand__sub">DENTAL CARE</span></span>
    </div>

    <ul class="contact">
      <li><svg viewBox="0 0 12 12"><circle cx="6" cy="6" r="5.5" fill="none" stroke="var(--green-deep)"/><path d="M4 3 L5 5 L4.5 5.5 Q5.5 7.5 6.5 7.5 L7 7 L9 8 Q8.5 9.5 7 9 Q3.5 8 3 4.5 Q3 3.2 4 3Z" fill="var(--green-deep)"/></svg>555-555-0174</li>
      <li><svg viewBox="0 0 12 12"><rect x="1" y="5" width="10" height="6" rx="1" fill="var(--green-deep)"/><rect x="3" y="1" width="6" height="4" fill="none" stroke="var(--green-deep)"/></svg>555-555-0189</li>
      <li><svg viewBox="0 0 12 12"><circle cx="6" cy="6" r="6" fill="var(--green-deep)"/><path d="M3 4 H9 V8.5 H3 Z M3 4 L6 6.5 L9 4" fill="none" stroke="#fff" stroke-width="0.9"/></svg>info@BrightwellDentalCareMi.com</li>
      <li><svg viewBox="0 0 12 12"><circle cx="6" cy="6" r="6" fill="var(--green-deep)"/><path d="M1 6 H11 M6 1 V11 M3.5 2.5 Q6 6 3.5 9.5 M8.5 2.5 Q6 6 8.5 9.5" fill="none" stroke="#fff" stroke-width="0.7"/></svg>www.BrigthwellDentalCareMi.com</li>
    </ul>

    <address class="address">
      2730 W. Halvert Rd. Ste.<br>
      7 Alderbrook, WA 48391
    </address>
  </section>

  <section class="card card--back" aria-label="Business card back">
    <div class="brand">
      <span class="brand__dot"></span>
      <span class="brand__name">Brightwell<span class="brand__sub">DENTAL CARE</span></span>
    </div>

    <div class="appointment">
      <h2 class="appointment__title">YOUR APPOINTMENT</h2>
      <div class="field-row">
        <span>Name :</span>
        <span class="field-line field-line--dotted" style="width:290px"></span>
      </div>
      <div class="field-row">
        <span>Date :</span>
        <span class="field-line" style="width:90px"></span>
        <span style="margin-left:14px">Time :</span>
        <span class="field-line" style="width:82px"></span>
        <span>am / pm</span>
      </div>
    </div>

    <p class="notice">If you are unable to keep your appointment, kindly give 48 hours notice</p>
  </section>

</body>
</html>
```